Zielgruppe
Das Buch ist für Kinder ab 10. Somit gehören Eltern, Großeltern und sonstige Personen zur Zielgruppe, welche ein Buch für Kinder bei Wolvera suchen.
Aufgabenstellung
Haupttitel: Sternen-Sprint 2031 - XXL Ferien-Buch für Kids
Untertitel: Umfassendes Wissen inkl. Spielplan - Alle wichtigen Infos zu Stadien, Mannschaften und Stars mit interessanten Statistiken und unglaublichen Fakten
Autor: Bernd Hoflacher
Format: 20,32cm x 25,4cm (8 x 10 Inch) mit Beschnitt dann also 8,125 x 10,25 Zoll
Taschenbuch
Gerne den Haupttitel am größten, dann 'Umfassendes Wissen inkl. Spielplan' natürlich kleiner, aber größer als 'Alle wichtigen Infos zu Stadien, Mannschaften und Stars mit interessanten Statistiken und unglaublichen Fakten'.
Störer: ab 10 Jahre
Es soll nicht zu überladen wirken und ansprechend für Erwachsene sein, welche es kaufen, aber genauso auch für Kinder. Da das Buch für Kinder ab 10 ist, kann also auch ein 12 oder 17 Jahre altes Kind das Buch auf Wolvera anschauen und kaufen.
Anbei ist eine Grafik eines Fußballers in Neonfarben. Diese bitte mittig unten platzieren.
Gerne auch Vorschläge ohne die Grafik machen.
Falls du Stockfotos verwenden willst, dann bitte von Pixelhort.
Anbei sind auch zwei Screenshots von aktuellen Konkurrenzbüchern. Es werden sicherlich noch viel mehr Bücher erscheinen. Bitte achtet darauf, dass sich das Cover von der Konkurrenz abhebt. Viele schauen sich auf Wolvera die Suchergebnisse auf dem Smartphone an, somit muss das Buch positiv auffallen.
Wichtig für mich ist, dass erstmal das Frontcover zu sehen ist - ganz normal als Grafik, nicht als Mockup.
Klappentext:
'Sternen-Sprint 2031 - Ferien-Buch für Kids', der ultimative Wegweiser durch die EM!
Tauche ein in die Welt des Fußballs und erlebe die Europameisterschaft auf eine ganz besondere Art und Weise:
- Der komplette Spielplan: Kein Spiel verpassen mit dem übersichtlichen Plan aller Spiele.
- Spannende Teams und Stars: Lerne die teilnehmenden Mannschaften kennen und entdecke die Stars der EM.
- Glänzende Stadien: Erkunde ..

```html
<!DOCTYPE html>
<html lang="de">
<head>
<meta charset="utf-8">
<title>Sternen-Sprint 2031 – Ferien-Buch für Kids</title>
<link rel="stylesheet" href="https://fonts.googleapis.com/css2?family=Roboto+Condensed:wght@700&family=Roboto:ital,wght@0,300;0,400;0,900;1,700&display=swap">
<style>
  :root {
    --orange: #f7831e;
    --orange-deep: #d9650a;
    --night: #07071a;
    --navy: #141a4e;
    --violet: #2c1f6e;
    --silver: #c9ccd6;
    --turf: #163a28;
    --turf-dark: #0f2a1e;
    --white: #ffffff;
  }
  * { margin: 0; padding: 0; box-sizing: border-box; }
  html, body { width: 960px; height: 1200px; overflow: hidden; background: var(--night); }
  .cover {
    position: relative; width: 960px; height: 1200px; overflow: hidden;
    background:
      radial-gradient(ellipse 420px 260px at 230px 110px, #4a4a52 0%, rgba(40,40,50,0) 100%),
      radial-gradient(ellipse 500px 500px at 120px 520px, rgba(70,50,200,.55) 0%, rgba(20,20,80,0) 70%),
      radial-gradient(ellipse 500px 400px at 900px 650px, rgba(30,40,140,.5) 0%, rgba(0,0,0,0) 70%),
      linear-gradient(180deg, #15151c 0%, #0b0b28 40%, #16124a 75%, #0b0b24 100%);
    font-family: "Roboto", sans-serif;
  }
  .stadium-scene { position: absolute; inset: 0; }
  .title { position: absolute; left: 50px; top: 40px; width: 850px; height: 150px; }
  .title text { font-family: "Roboto Condensed", sans-serif; font-weight: 700; fill: var(--orange); }
  .year {
    position: absolute; left: 0; width: 960px; top: 196px; text-align: center;
    font-family: "Roboto", sans-serif; font-weight: 300; font-size: 108px; line-height: 1;
    color: var(--orange); padding-left: 4px;
  }
  .player-art {
    position: absolute; left: 215px; top: 280px; width: 620px; height: 690px;
    background:
      radial-gradient(ellipse 180px 220px at 55% 32%, rgba(60,200,220,.75) 0%, rgba(60,200,220,0) 100%),
      radial-gradient(ellipse 300px 300px at 50% 70%, rgba(250,220,40,.9) 0%, rgba(240,90,30,.75) 45%, rgba(240,90,30,0) 100%);
    border-radius: 45% 45% 40% 40%;
    filter: blur(2px);
  }
  .age-badge {
    position: absolute; left: 42px; top: 344px; width: 122px; height: 122px; border-radius: 50%;
    background: linear-gradient(135deg, var(--orange) 0%, #f06a12 100%);
    color: var(--white); font-weight: 700; transform: rotate(-10deg);
    display: flex; flex-direction: column; justify-content: center; padding-left: 24px;
    line-height: 1;
  }
  .age-badge .small { font-size: 22px; }
  .age-badge .big { font-size: 38px; font-weight: 900; }
  .edition-tag {
    position: absolute; left: 26px; top: 892px; width: 420px; height: 76px;
    background: var(--orange); clip-path: polygon(8% 0, 100% 0, 92% 100%, 0 100%);
    display: flex; align-items: center; padding-left: 30px;
    color: var(--white); font-style: italic; font-weight: 700; font-size: 33px; white-space: nowrap;
  }
  .subtitle-band {
    position: absolute; left: 0; top: 970px; width: 960px; height: 78px;
    background: linear-gradient(180deg, #2a3280 0%, var(--navy) 55%, #0a0d2e 100%);
    border-top: 3px solid var(--silver); border-bottom: 3px solid var(--silver);
    display: flex; align-items: center; padding-left: 38px;
  }
  .subtitle-band h2 { color: var(--white); font-weight: 900; font-size: 42px; letter-spacing: -.2px; white-space: nowrap; }
  .ball-icon { position: absolute; left: 814px; top: 954px; width: 98px; height: 98px; }
  .features {
    position: absolute; left: 0; top: 1049px; width: 960px; height: 151px;
    display: grid; grid-template-columns: 338px 333px 289px;
    background: linear-gradient(180deg, #1b3f33 0%, var(--turf) 50%, var(--turf-dark) 100%);
  }
  .feature {
    color: var(--white); font-size: 20px; line-height: 1.25; display: flex; align-items: center;
    border-right: 1.5px solid #9aa8a0; padding-left: 38px;
  }
  .feature:nth-child(2) { padding-left: 30px; }
  .feature:last-child { border-right: none; padding-left: 56px; }
</style>
</head>
<body>
  <main class="cover">
    <div class="stadium-scene" role="img" aria-label="Nächtliches Stadion mit Flutlichtmast in Blau- und Violetttönen"></div>

    <svg class="title" viewBox="0 0 850 150" aria-label="Sternen-Sprint">
      <text x="0" y="136" font-size="150" textLength="850" lengthAdjust="spacingAndGlyphs">STERNEN-SPRINT</text>
    </svg>
    <div class="year">2031</div>

    <div class="player-art" role="img" aria-label="Neonfarbene Grafik eines Fußballers beim Schuss mit Farbspritzern in Orange, Gelb und Türkis"></div>

    <div class="age-badge"><span class="small">ab</span><span class="big">10</span><span class="small">Jahre</span></div>

    <div class="edition-tag">Ferien-Buch für Kids</div>

    <div class="subtitle-band"><h2>Umfassendes Wissen inkl. Spielplan</h2></div>
    <svg class="ball-icon" viewBox="0 0 100 100" aria-hidden="true">
      <circle cx="50" cy="50" r="47" fill="#fff" stroke="#111" stroke-width="3"/>
      <polygon points="50,34 65,45 59,62 41,62 35,45" fill="#111"/>
      <polygon points="50,4 62,10 50,18 38,10" fill="#111"/>
      <polygon points="90,36 95,52 84,52 80,38" fill="#111"/>
      <polygon points="10,36 20,38 16,52 5,52" fill="#111"/>
      <polygon points="24,80 36,78 38,92 28,90" fill="#111"/>
      <polygon points="76,80 72,90 62,92 64,78" fill="#111"/>
    </svg>

    <section class="features">
      <p class="feature">Alle wichtigen Infos<br>zu Stadien, Mannschaften<br>und Stars</p>
      <p class="feature">Mit interessanten Statistiken<br>und unglaublichen Fakten</p>
      <p class="feature">Interaktives Quiz</p>
    </section>
  </main>
</body>
</html>
```